The most modern business card ever !!!

Our company call “Vendalo”. Vendalo is a technology company specialized in cruises solutions. Out main product is a platform to reserve cruises. This is a revolutionary platform that make easier to travel agencies and final users to reserve cruises across dozen companies like tibba, wernu, hpv, dgb, etc..We are a “start up”, with a young team of developers and we want to transmit it.. For it, we want something different, a modern business card that represent cruises and technology.. When someone receive this card, this person should say: wowww this is different… this is modern… this is a cruise related company..
- diferent, modern
- traditions business card

```html
<!DOCTYPE html>
<html lang="pt-BR">
<head>
<meta charset="utf-8">
<title>Vendalo – Business Card</title>
<link href="https://fonts.googleapis.com/css2?family=Exo+2:wght@400;500;600;700&display=swap" rel="stylesheet">
<style>
  :root {
    --backdrop: #d9dadc;
    --card: #f4f4f2;
    --ink: #1d1d1d;
    --accent: #1f9fcf;
    --dark: #101214;
  }
  * { margin: 0; padding: 0; box-sizing: border-box; }
  html, body { width: 1200px; height: 971px; overflow: hidden; }
  body {
    background: var(--backdrop);
    font-family: "Exo 2", Arial, sans-serif;
    color: var(--ink);
    position: relative;
  }
  .card {
    position: absolute;
    left: 150px; top: 205px;
    width: 900px; height: 560px;
    background: var(--card);
    border-radius: 26px;
    overflow: hidden;
    box-shadow: 0 10px 30px rgba(0,0,0,0.12);
  }
  .card__feature {
    position: absolute;
    top: 0; right: 0;
    width: 250px; height: 100%;
    background: linear-gradient(160deg, var(--accent) 0%, #176e94 45%, var(--dark) 100%);
  }
  .brand {
    position: absolute; left: 56px; top: 58px;
    font-size: 74px; font-weight: 500; letter-spacing: 1px;
    color: var(--ink); line-height: 1;
  }
  .person { position: absolute; left: 60px; top: 196px; }
  .person__name { font-size: 31px; font-weight: 600; color: var(--accent); line-height: 1.1; }
  .person__role { font-size: 23px; font-weight: 400; margin-top: 4px; }
  .address { position: absolute; left: 64px; top: 300px; font-size: 23px; line-height: 30px; font-style: normal; }
  .address__company { font-weight: 700; }
  .contacts { position: absolute; left: 68px; top: 440px; list-style: none; font-size: 23px; line-height: 31px; }
  .contacts li { display: flex; align-items: center; gap: 10px; }
  .contacts svg { width: 20px; height: 20px; flex: none; }
</style>
</head>
<body>
  <article class="card">
    <div class="card__feature" role="img" aria-label="Angular blue and black decorative graphic on the right edge of the card"></div>

    <div class="brand">Vendalo</div>

    <div class="person">
      <div class="person__name">Marcus Delane</div>
      <div class="person__role">Developer</div>
    </div>

    <address class="address">
      <div class="address__company">Vendalo Tecnologia Em Informatica Eireli</div>
      <div>R Almirante Tavora Reis 418</div>
      <div>Sala 17, Vila Mariscal</div>
      <div>Campo Verde, SP, 09145-320, Brasil</div>
    </address>

    <ul class="contacts">
      <li>
        <svg viewBox="0 0 24 24" aria-hidden="true"><path fill="var(--accent)" d="M6.6 10.8a15.1 15.1 0 0 0 6.6 6.6l2.2-2.2c.3-.3.7-.4 1-.2 1.1.4 2.3.6 3.6.6.6 0 1 .4 1 1V20c0 .6-.4 1-1 1A17 17 0 0 1 3 4c0-.6.4-1 1-1h3.5c.6 0 1 .4 1 1 0 1.3.2 2.5.6 3.6.1.3 0 .7-.2 1z"/></svg>
        (11) 9482-3175
      </li>
      <li>
        <svg viewBox="0 0 24 24" aria-hidden="true"><rect x="2" y="5" width="20" height="14" rx="1" fill="none" stroke="var(--accent)" stroke-width="2"/><path d="M2 6l10 7 10-7" fill="none" stroke="var(--accent)" stroke-width="2"/></svg>
        marcus@vendalo.com.br
      </li>
      <li>
        <svg viewBox="0 0 24 24" aria-hidden="true"><circle cx="12" cy="12" r="10" fill="none" stroke="var(--accent)" stroke-width="2"/><path d="M2 12h20M12 2c3 3 3 17 0 20M12 2c-3 3-3 17 0 20" fill="none" stroke="var(--accent)" stroke-width="1.6"/></svg>
        www.vendalo.com.br
      </li>
    </ul>
  </article>
</body>
</html>
```